Business Card Design for Online Gift Business

Business card design for a new online Canadian company called "Harlow & Brine Gift Boxes" selling modern and luxurious gift boxes for every occasion. Items are sourced locally from talented socially-responsible Canadian artisans. Each gift is elegantly presented in a keepsake wood box to ensure a lasting impression.

Industry/Entity Type

E-Commerce

Contact Information for Business Card

Marla Whitcombe, Proprietor
Kelowna, BC
403-555-2741
www.harlowandbrine.ca
hello@harlowandbrine.ca

Requirements
Must have
• Keepsakes made well, for those you love
• Please also include the symbols for Pagebook and Picturegram
Nice to have
• **I have attached a few samples of background colors and font colors that I like. I hope this helps in a few directions to try.

```html
<!DOCTYPE html>
<html lang="en">
<head>
<meta charset="utf-8">
<title>Harlow &amp; Brine Gift Boxes – Business Card</title>
<link rel="stylesheet" href="https://fonts.googleapis.com/css2?family=Cinzel:wght@400;500&family=Parisienne&display=swap">
<style>
  :root {
    --page: #ebebeb;
    --card-top: #d3cab8;
    --card-bottom: #c6bba6;
    --ink: #3a3632;
    --brand: #6e4c2c;
    --band: #a39570;
    --band-ink: #2f2a22;
    --leaf-tint: rgba(255, 255, 255, 0.18);
  }
  * { margin: 0; padding: 0; box-sizing: border-box; }
  html, body {
    width: 1200px; height: 576px; overflow: hidden;
    background: var(--page);
  }
  .canvas { position: relative; width: 1200px; height: 576px; }
  .card {
    position: absolute; top: 139px;
    width: 485px; height: 293px;
    border-radius: 7px;
    background: linear-gradient(180deg, var(--card-top), var(--card-bottom));
    font-family: "Cinzel", serif;
    color: var(--ink);
    overflow: hidden;
  }
  .card--front { left: 82px; }
  .card--back { left: 602px; width: 481px; }

  .brand-name {
    position: absolute; left: 0; right: 0; top: 110px;
    text-align: center;
    font-family: "Cinzel", serif; font-weight: 500;
    font-size: 28px; line-height: 36px; letter-spacing: 2px;
    color: var(--brand);
  }
  .follow {
    position: absolute; left: 0; right: 0; top: 242px;
    display: flex; justify-content: center; align-items: center; gap: 6px;
    font-size: 10px; line-height: 14px; letter-spacing: 0.5px;
  }
  .follow .network { display: flex; align-items: center; gap: 3px; }
  .follow .dot { width: 10px; height: 10px; border-radius: 2px; background: var(--ink); }

  .leaf-area {
    position: absolute; left: 106px; top: 34px; width: 264px; height: 252px;
    background: radial-gradient(ellipse at center, var(--leaf-tint), transparent 70%);
  }
  .holder-name {
    position: absolute; left: 0; right: 0; top: 56px;
    text-align: center;
    font-family: "Parisienne", cursive; font-weight: 400;
    font-size: 38px; line-height: 40px;
    color: var(--ink);
  }
  .holder-role {
    position: absolute; left: 0; right: 0; top: 96px;
    text-align: center; font-size: 12px; line-height: 16px; letter-spacing: 0.5px;
  }
  .contact {
    position: absolute; left: 0; right: 0; top: 145px;
    list-style: none; text-align: center;
    font-size: 13px; line-height: 18px;
  }
  .tagline-band {
    position: absolute; left: 0; right: 0; top: 251px; height: 22px;
    background: var(--band);
    display: flex; align-items: center; justify-content: center;
    font-size: 13px; letter-spacing: 0.3px; color: var(--band-ink);
    white-space: nowrap;
  }
</style>
</head>
<body>
<main class="canvas">
  <section class="card card--front" aria-label="Card front">
    <h1 class="brand-name">Harlow &amp; Brine</h1>
    <div class="follow">
      <span>Follow us:</span>
      <span class="network"><span class="dot"></span>Pagebook</span>
      <span class="network"><span class="dot"></span>Picturegram</span>
    </div>
  </section>

  <section class="card card--back" aria-label="Card back">
    <div class="leaf-area" role="img" aria-label="Faint decorative brand symbol"></div>
    <h2 class="holder-name">Marla Whitcombe</h2>
    <p class="holder-role">Proprietor</p>
    <ul class="contact">
      <li>Kelowna, BC</li>
      <li>403-555-2741</li>
      <li>www.harlowandbrine.ca</li>
      <li>hello@harlowandbrine.ca</li>
    </ul>
    <p class="tagline-band">Keepsakes made well, for those you love</p>
  </section>
</main>
</body>
</html>
```